Business Card for premium dental clinic

We are a premium dental clinic based in Brasov, Romania with more than 15 year on the market, providing quality dental treatment made by a team of more specialized dentists, working with modern equipment as a solution to beautiful and healthy teeth.

Our current logo for the clinic use 2 square with colors black and gold - dr Ternisu - studio, using family fonts Bodoni, Myriad Pro and Segoe Print.
Depending on the printing we used some gold CMYK background or gold foil picture background or a gold gradient.
We want a business card:
- eye catching business card
- distinguished business card
- premium design
- to keep the color scheme of black and gold
- to attract the customers to spent time reading the information
- modern concept

```html
<!DOCTYPE html>
<html lang="en">
<head>
<meta charset="utf-8">
<title>dr Ternisu – business card</title>
<link href="https://fonts.googleapis.com/css2?family=Lato:wght@400;700;900&display=swap" rel="stylesheet">
<style>
  :root {
    --stage: #2a2a2b;
    --card: #1c1d1f;
    --card-back: #151516;
    --gold: #c08f2c;
    --white: #f2f2f2;
    --rule: #6b6b6b;
    --pattern-a: #1a1a1b;
    --pattern-b: #202022;
  }
  html, body {
    margin: 0;
    padding: 0;
    width: 1200px;
    height: 1108px;
    overflow: hidden;
    background: var(--stage);
    font-family: "Lato", Arial, sans-serif;
  }
  .stage {
    position: relative;
    width: 1200px;
    height: 1108px;
  }
  .card {
    position: absolute;
    top: 230px;
    width: 380px;
    height: 640px;
    border-radius: 26px;
    box-shadow: 0 18px 40px rgba(0,0,0,.45);
    overflow: hidden;
  }
  .card--front {
    left: 170px;
    background: var(--card);
    text-align: center;
    color: var(--white);
  }
  .card--back {
    left: 650px;
    background: var(--card-back);
  }

  .brand-name {
    margin: 0;
    color: var(--white);
    font-weight: 700;
    white-space: nowrap;
  }
  .card--front .brand-name {
    margin-top: 130px;
    font-size: 36px;
    letter-spacing: .5px;
  }

  .person__name {
    margin: 150px 0 0;
    color: var(--gold);
    font-weight: 900;
    font-size: 28px;
    letter-spacing: .5px;
    text-transform: uppercase;
    white-space: nowrap;
  }
  .person__role {
    margin: 4px 0 0;
    font-size: 19px;
  }

  .contact-rule {
    display: flex;
    align-items: center;
    gap: 8px;
    margin: 16px 44px 12px;
  }
  .contact-rule::before,
  .contact-rule::after {
    content: "";
    flex: 1;
    height: 1px;
    background: var(--rule);
  }
  .contact-icon {
    width: 30px;
    height: 30px;
  }
  .contact-list {
    list-style: none;
    margin: 0;
    padding: 0;
    font-size: 19px;
    line-height: 1.35;
  }
  .divider {
    height: 1px;
    background: var(--rule);
    margin: 14px 44px;
  }
  .address {
    font-style: normal;
    font-size: 19px;
    line-height: 1.35;
  }

  .back-pattern {
    position: absolute;
    inset: 0;
    background:
      repeating-linear-gradient(0deg, transparent 0 78px, var(--pattern-b) 78px 82px),
      repeating-linear-gradient(90deg, var(--pattern-a) 0 128px, var(--pattern-b) 128px 132px);
  }
  .back-badge {
    position: absolute;
    left: 50%;
    top: 50%;
    transform: translate(-50%, -50%);
    padding: 22px 34px;
    background: var(--card-back);
    border: 1px solid #2c2c2e;
  }
  .card--back .brand-name {
    font-size: 26px;
  }
</style>
</head>
<body>
<main class="stage">

  <section class="card card--front" aria-label="Business card front">
    <p class="brand-name">dr Ternisu</p>

    <h1 class="person__name">Mihai Dorobanțu</h1>
    <p class="person__role">Managing Director</p>

    <div class="contact-rule">
      <svg class="contact-icon" viewBox="0 0 30 30" aria-label="phone" role="img">
        <circle cx="15" cy="15" r="15" fill="#c08f2c"/>
        <path d="M10 9c1-1 2-1 2.6 0l1.4 2.3c.4.7.2 1.3-.4 1.8l-.8.6c.8 1.7 2 2.9 3.6 3.7l.6-.8c.5-.6 1.1-.8 1.8-.4l2.3 1.4c1 .6 1 1.6 0 2.6-1.2 1.2-3 1.4-5 .3-2.6-1.4-4.8-3.6-6.2-6.2-1-2-.8-3.8.1-5.3z" fill="#1c1d1f"/>
      </svg>
      <svg class="contact-icon" viewBox="0 0 30 30" aria-label="email" role="img">
        <circle cx="15" cy="15" r="15" fill="#c08f2c"/>
        <rect x="8" y="10" width="14" height="10" rx="1" fill="#1c1d1f"/>
        <path d="M8.5 10.5 15 16l6.5-5.5" fill="none" stroke="#c08f2c" stroke-width="1.3"/>
      </svg>
      <svg class="contact-icon" viewBox="0 0 30 30" aria-label="website" role="img">
        <circle cx="15" cy="15" r="15" fill="#c08f2c"/>
        <circle cx="15" cy="15" r="7" fill="none" stroke="#1c1d1f" stroke-width="1.6"/>
        <ellipse cx="15" cy="15" rx="3" ry="7" fill="none" stroke="#1c1d1f" stroke-width="1.4"/>
        <path d="M8 15h14" stroke="#1c1d1f" stroke-width="1.4"/>
      </svg>
    </div>

    <ul class="contact-list">
      <li>0268 - 412 905</li>
      <li>contact@ternisu.ro</li>
      <li>www.ternisu.ro</li>
    </ul>

    <div class="divider"></div>

    <address class="address">
      421, Address line here,<br>
      45452, Country name
    </address>
  </section>

  <section class="card card--back" aria-label="Business card back">
    <div class="back-pattern" role="img" aria-label="Faint repeated tile pattern in dark tones"></div>
    <div class="back-badge">
      <p class="brand-name">dr Ternisu</p>
    </div>
  </section>

</main>
</body>
</html>
```